CPA Graduation Party

I need to make simple invitation for my sister's recent success, passing the CPA (Certified Public Accountant) exam. It is a surprise party. I want very simple and professional looking invitation. My only requirements are that you don't use any graduation caps or gowns due to the fact that it's not an actual graduation. It's a series of exams that she passes. Be creative with the design but once again, keep it professional. I have attached a font called iScriptSTD. I liked the font so was thinking about using it. But it's not necessary. If you have something slimier or better, please use it.

I was planning on printing on a specific kind of paper. It's called pearlized ivory cardstock. It has a little coating and shine on it and since it's ivory, I was thinking about the main color of the invitation to be burgundy type. For example, see the following RGB: R204, G0, B102.

Party info:
Name: Revathi
Date & Time: Saturday, March 8th, 2014 at 6:00pm
Location: Kesar Mahal. 413 Weaverly Lane Parsippany, NJ 07089

I know I didn't provide a lot of info for the invite but please be creative.  Use general knowledge and other formal party invites as examples. I am not looking for a name, date and location as three bullets on the card.

Also, I forgot to mention the size of the invite.  It should be 5.5x8.5.  Thank you.

• graduation caps and/or gowns

```html
<!DOCTYPE html>
<html lang="en">
<head>
<meta charset="utf-8">
<title>Surprise Party Invitation – Revathi</title>
<link rel="stylesheet" href="https://fonts.googleapis.com/css2?family=Courgette&display=swap">
<style>
  :root {
    --canvas-bg: #ffffff;
    --card-bg: #f0f0f0;
    --berry: #cc0066;
    --berry-band: #aa0066;
    --berry-shade: #7a0044;
    --ink-light: #ffffff;
  }
  * { margin: 0; padding: 0; box-sizing: border-box; }
  html, body {
    width: 1200px;
    height: 1000px;
    overflow: hidden;
    background: var(--canvas-bg);
  }
  .invitation {
    position: relative;
    width: 1200px;
    height: 1000px;
    font-family: "Courgette", cursive;
    color: var(--berry);
  }
  .ribbon-art {
    position: absolute;
    inset: 0;
  }
  .line {
    position: absolute;
    left: 0;
    width: 1200px;
    text-align: center;
    white-space: nowrap;
    line-height: 1;
  }
  .heading-label { top: 242px; font-size: 25px; color: var(--ink-light); }
  .for-label     { top: 289px; font-size: 23px; }
  .guest-name    { top: 322px; font-size: 70px; letter-spacing: 1px; }
  .occasion      { top: 412px; font-size: 22px; }
  .tag-label     { font-size: 16px; color: var(--ink-light); }
  .tag-on        { top: 474px; }
  .tag-at        { top: 578px; }
  .event-date    { top: 527px; font-size: 24px; }
  .venue         { top: 633px; font-size: 24px; }
  .rsvp          { top: 711px; font-size: 20px; color: var(--ink-light); }
</style>
</head>
<body>
<main class="invitation">
  <svg class="ribbon-art" width="1200" height="1000" viewBox="0 0 1200 1000" aria-hidden="true">
    <rect class="card" x="119" y="179" width="968" height="626" fill="var(--card-bg)"/>
    <!-- top banner -->
    <rect class="banner-band" x="119" y="251" width="968" height="43" fill="var(--berry-band)"/>
    <rect x="524" y="277" width="175" height="17" fill="var(--card-bg)"/>
    <polygon points="467,277 524,277 524,294" fill="var(--berry-shade)"/>
    <polygon points="755,277 699,277 699,294" fill="var(--berry-shade)"/>
    <rect class="banner-face" x="467" y="234" width="288" height="43" fill="var(--berry)"/>
    <!-- "On" tag -->
    <g class="tag">
      <polygon points="551,481 603,481 603,506 551,506 564,493.5" fill="var(--berry-band)"/>
      <polygon points="680,481 628,481 628,506 680,506 667,493.5" fill="var(--berry-band)"/>
      <polygon points="581,497 603,497 603,506" fill="var(--berry-shade)"/>
      <polygon points="650,497 628,497 628,506" fill="var(--berry-shade)"/>
      <rect x="581" y="469" width="69" height="28" fill="var(--berry)"/>
    </g>
    <!-- "At" tag -->
    <g class="tag">
      <polygon points="551,585 603,585 603,610 551,610 564,597.5" fill="var(--berry-band)"/>
      <polygon points="680,585 628,585 628,610 680,610 667,597.5" fill="var(--berry-band)"/>
      <polygon points="581,601 603,601 603,610" fill="var(--berry-shade)"/>
      <polygon points="650,601 628,601 628,610" fill="var(--berry-shade)"/>
      <rect x="581" y="573" width="69" height="28" fill="var(--berry)"/>
    </g>
    <!-- RSVP band -->
    <rect class="rsvp-band" x="119" y="701" width="968" height="43" fill="var(--berry)"/>
  </svg>

  <p class="line heading-label">Surprise Party</p>
  <p class="line for-label">For</p>
  <h1 class="line guest-name">REVATHI</h1>
  <p class="line occasion">to celebrate her passing the CPA exam</p>
  <p class="line tag-label tag-on">On</p>
  <p class="line event-date">Saturday, March 8th, 2014 at 6.00 pm</p>
  <p class="line tag-label tag-at">At</p>
  <p class="line venue">Kesar Mahal. 413 Weaverly Lane Parsippany, NJ 07089</p>
  <p class="line rsvp">RSVP at rsvp.nmehta@inboxmail.com or call (405) 555 - 0182</p>
</main>
</body>
</html>
```